Kestrel Motion LLC Sports Therapy and Soft Tissue Injury solutions

We are a company that specializes in Sports Therapy, Physical therapy, muscular rehab, nutrition plans, and personal training. Kestrel Motion travels around the country and world treating athletes and people in the workforce that have Soft Tissue injuries. We are legally partnered with VMR(Vantor Muscle Recovery/vantorrecovery.example) in treating endurance athletes ex. SteelRidge triathalon. We educate our patients on how to sustain a healthy lifestyle.We need a web design that has a Home page summarizing our services, a Physical therapy page, a Personal training and nutrition page. Our ultimate goal is to build relationships with fitness centers, training facilities, and companies that are implementing preventative health measures for their employees. We want to incorporate the VMR logo and Steelridge logo attached in the website but, we want to use our own name (Kestrel Motion LLC) as the main draw. We will provide literature for the website.

Target Market(s)

Grindlane training gyms, Fitness centers, Dance studios, Companies looking for Corporate Wellness programs

Industry/Entity Type

Health And Wellness

Number of Pages Required

4 page

Font styles to use
Sans Serif

Requirements
Must have
• Stock Photos of Athletes training. Examples of Endurance Athletes and Cross training. A mesh of as many sports and training methods as possible. We are a new company and don't have many photos. Easy accessibility to change and add text as the company grows. Vantor Muscle recovery logo incorporated in the back ground of the website. Always visible but does not take over the web page
Nice to have
• Sleek and cool, and masculine design. We want the website to stand out without focusing on one individual. We want to use the website to brand the company (Kestrel Motion LLC) with easy access to social media platforms

```html
<!DOCTYPE html>
<html lang="en">
<head>
<meta charset="utf-8">
<title>Kestrel Motion LLC — Sports Therapy</title>
<link href="https://fonts.googleapis.com/css2?family=Roboto:wght@400;500;700&family=Open+Sans:wght@400;600&display=swap" rel="stylesheet">
<style>
:root{
  --blue:#4a5fa8;
  --blue-dark:#3f5399;
  --blue-band:#4458a0;
  --nav:#555759;
  --grey-mid:#737373;
  --grey-light:#8e8e8e;
  --ink:#222;
  --text:#333;
  --muted:#666;
  --footer-bg:#f4f4f4;
  --partner-bg:#2e2e2e;
  --white:#fff;
}
*{margin:0;padding:0;box-sizing:border-box}
html,body{width:1200px;height:2493px;overflow:hidden;background:var(--white)}
body{position:relative;font-family:'Open Sans',sans-serif;color:var(--text)}
.abs{position:absolute}
h1,h2,h3,.nav a,.btn{font-family:'Roboto',sans-serif}

/* header */
.site-header{left:0;top:0;width:1200px;height:83px}
.brand{left:133px;top:22px;display:flex;align-items:center;gap:12px;font-family:'Roboto',sans-serif;font-weight:500;font-size:29px;color:#3a3f4a}
.brand-dot{width:24px;height:24px;border-radius:50%;background:var(--blue)}
.helpline{right:337px;top:31px;font-size:12.5px;color:#555;display:flex;align-items:center;gap:7px;white-space:nowrap}
.helpline strong{font-weight:400;color:var(--blue);font-size:16px}
.appt{left:889px;top:24px;width:176px;height:37px;background:var(--blue);color:#fff;font-size:12px;font-weight:500;display:flex;align-items:center;justify-content:center;border-radius:2px;letter-spacing:.3px}

/* nav */
.nav{left:0;top:83px;width:1200px;height:42px;background:linear-gradient(#5f6163,#4b4d4f)}
.nav ul{list-style:none;display:flex;margin-left:133px;height:42px}
.nav a{display:flex;align-items:center;height:42px;padding:0 28px;color:#fff;font-size:12px;text-decoration:none;border-right:1px solid #6b6d6f}
.nav a.active{background:var(--blue)}

/* hero */
.hero{left:0;top:125px;width:1200px;height:473px;background:linear-gradient(100deg,#b07f4e 0%,#d9a46a 22%,#e8c9a2 45%,#b9c2cf 70%,#8793a8 100%)}
.hero-title{left:133px;top:250px;font-size:56px;font-weight:700;color:#fff;text-shadow:0 2px 6px rgba(0,0,0,.35);letter-spacing:1px}
.hero-copy{left:133px;top:336px;width:470px;font-size:12px;line-height:20px;color:#222}
.btn{display:flex;align-items:center;justify-content:center;background:var(--blue);color:#fff;font-size:12px;border-radius:2px}
.hero-btn{left:133px;top:400px;width:122px;height:42px}
.dots{left:133px;top:486px;display:flex;gap:6px}
.dots span{width:8px;height:8px;border-radius:50%;background:#c9c9c9}
.dots span:first-child{background:var(--blue)}

/* feature boxes */
.features{left:133px;top:598px;width:934px;height:167px;display:flex}
.feature{flex:1;display:flex;flex-direction:column;align-items:center;color:#fff;padding-top:38px}
.feature h3{font-weight:400;font-size:21px;margin-top:16px}
.feature p{font-size:11px;margin-top:10px}
.f1{background:var(--blue)}.f2{background:var(--grey-mid)}.f3{background:var(--grey-light)}
.feature-shadow{left:233px;top:765px;width:734px;height:60px;background:radial-gradient(ellipse at 50% 0%,rgba(0,0,0,.22),rgba(0,0,0,0) 65%)}

/* welcome */
.welcome-title{left:133px;top:856px;font-size:29px;font-weight:400;color:var(--ink)}
.welcome-copy{left:133px;top:915px;width:500px;font-size:10.4px;line-height:20px;color:#333;text-align:justify}
.welcome-copy p+p{margin-top:20px}
.welcome-btn{left:133px;top:1103px;width:90px;height:31px;font-size:11px}
.video-frame{left:661px;top:859px;width:404px;height:276px;border:1px solid #ddd;padding:7px;background:#fff;box-shadow:0 0 6px rgba(0,0,0,.15)}
.video-fill{width:100%;height:100%;background:linear-gradient(120deg,#6f9a5c 0%,#a9c18f 30%,#e7c9b0 55%,#d9ab8c 100%);position:relative}
.play{position:absolute;left:50%;top:50%;transform:translate(-50%,-60%)}

/* services */
.services{left:0;top:1193px;width:1200px;height:411px;background:linear-gradient(180deg,#4b5ea6,var(--blue-band))}
.services h2{position:absolute;left:0;width:1200px;top:74px;text-align:center;color:#fff;font-weight:400;font-size:29px}
.cards{position:absolute;left:133px;top:147px;display:flex;gap:21px}
.card{width:219px;height:209px;background:#fff;padding:2px}
.card-img{height:164px}
.card h3{font-weight:400;font-size:15px;color:var(--blue-dark);text-align:center;margin-top:14px;letter-spacing:.3px}
.c1{background:linear-gradient(135deg,#d8b59c,#eee6dc)}
.c2{background:linear-gradient(135deg,#e9e4de,#c9d6e6)}
.c3{background:linear-gradient(135deg,#cfc3b3,#f1ece6)}
.c4{background:linear-gradient(135deg,#f1f1f1,#e7c67a)}

/* soft tissue */
.tissue-frame{left:130px;top:1667px;width:405px;height:278px;border:1px solid #ddd;padding:7px;background:#fff;box-shadow:0 0 6px rgba(0,0,0,.15)}
.tissue-fill{width:100%;height:100%;background:linear-gradient(90deg,#d9d9d9 0%,#c9a793 35%,#e8e3dd 60%,#9fbf86 100%)}
.tissue-title{left:568px;top:1670px;font-size:29px;font-weight:400;color:var(--ink)}
.tissue-copy{left:568px;top:1717px;width:498px;font-size:10.4px;line-height:20px;color:#333;text-align:justify}
.tissue-copy p+p{margin-top:20px}
.tissue-btn{left:568px;top:1913px;width:91px;height:31px;font-size:11px}

/* partners */
.partners{left:0;top:2003px;width:1200px;height:171px;background:var(--partner-bg)}
.badge{position:absolute;top:30px;height:106px;border:1px solid #777;display:flex;align-items:center;justify-content:center;gap:16px}
.b1{left:361px;width:192px}
.b2{left:573px;width:266px}
.shape{height:30px;border-radius:15px}

/* footer */
.footer{left:0;top:2174px;width:1200px;height:319px;background:var(--footer-bg)}
.footer h4{font-family:'Roboto',sans-serif;font-weight:500;font-size:11px;color:#333;position:absolute;top:40px;letter-spacing:.3px}
.fcol{position:absolute;font-size:10.5px;color:#555}
.contact-list{left:133px;top:78px;list-style:none}
.contact-list li{display:flex;gap:14px;align-items:flex-start;margin-bottom:11px;line-height:13px}
.contact-list a{color:#555}
.links{left:389px;top:78px;list-style:none}
.links li{margin-bottom:10px}
.news{left:566px;top:78px;width:260px;line-height:22px}
.mail-input{position:absolute;left:566px;top:138px;width:251px;height:40px;border:1px solid #ddd;background:#fff;font-size:10.5px;color:#555;padding:12px 15px}
.subscribe{left:568px;top:192px;width:81px;height:27px;font-size:9px}
.socials{left:889px;top:38px;display:flex;gap:6px}
.socials span{width:30px;height:30px;border:1.5px solid #444;border-radius:50%}
.rule{left:133px;top:260px;width:938px;height:1px;background:#ccc}
.copy{left:0;top:280px;width:1200px;text-align:center;font-size:10px;color:#777}
</style>
</head>
<body>

<header class="abs site-header">
  <div class="abs brand"><span class="brand-dot"></span>Kestrel Motion LLC</div>
  <div class="abs helpline">
    <svg width="12" height="12" viewBox="0 0 24 24"><path fill="#3f5399" d="M6.6 10.8a15 15 0 0 0 6.6 6.6l2.2-2.2a1 1 0 0 1 1-.25 11.4 11.4 0 0 0 3.6.6 1 1 0 0 1 1 1V20a1 1 0 0 1-1 1A17 17 0 0 1 3 4a1 1 0 0 1 1-1h3.5a1 1 0 0 1 1 1c0 1.25.2 2.45.6 3.6a1 1 0 0 1-.25 1z"/></svg>
    New patient helpline <strong>(555)214-0387</strong>
  </div>
  <div class="abs btn appt">MAKE AN APPOINTMENT</div>
</header>

<nav class="abs nav">
  <ul>
    <li><a class="active">HOME</a></li>
    <li><a>SERVICES</a></li>
    <li><a>PHYSICAL THERAPY</a></li>
    <li><a>PERSONAL TRAINING</a></li>
    <li><a>NUTRITION</a></li>
    <li><a>CONTACT US</a></li>
  </ul>
</nav>

<section class="abs hero" role="img" aria-label="Two runners jogging on a trail at sunset among tall trees"></section>
<h1 class="abs hero-title">SPORTS THERAPY</h1>
<p class="abs hero-copy">Kestrel Motion travels around the country and world treating athletes and people in the workforce that have Soft Tissue injuries.</p>
<div class="abs btn hero-btn">READ MORE</div>
<div class="abs dots"><span></span><span></span><span></span></div>

<section class="abs features">
  <div class="feature f1">
    <svg width="36" height="36" viewBox="0 0 36 36" fill="none" stroke="#fff" stroke-width="2"><circle cx="22" cy="6" r="3"/><path d="M6 26h24M20 10l-6 10h10M8 20l6 0M12 26v6M26 26v6"/></svg>
    <h3>PHYSICAL THERAPY</h3><p>around the country</p>
  </div>
  <div class="feature f2">
    <svg width="36" height="36" viewBox="0 0 36 36" fill="none" stroke="#fff" stroke-width="2"><circle cx="18" cy="5" r="3"/><path d="M12 12h12v10h-3v12h-6V22h-3z"/></svg>
    <h3>PERSONAL TRAINING</h3><p>around the country</p>
  </div>
  <div class="feature f3">
    <svg width="36" height="36" viewBox="0 0 36 36"><path fill="#fff" d="M6 30C6 14 16 6 32 5c0 16-8 25-22 24l-3 4-2-1 3-4z"/></svg>
    <h3>NUTRITION</h3><p>around the country</p>
  </div>
</section>
<div class="abs feature-shadow"></div>

<h2 class="abs welcome-title">WELCOME TO KESTREL MOTION</h2>
<div class="abs welcome-copy">
  <p>Kestrel Motion Mission statement-We are a company that specializes in Sports Therapy, Physical therapy, muscular rehab, nutrition plans, and personal training. Kestrel Motion travels aroundthe country and world treating athletes and people in the workforce that have Soft tissue injuries. Weeducate our patients on how to sustain a healthy lifestyle!</p>
  <p>We build relationships with companies committed to the sustainable health of their employees and patrons. We offer Corporate Health Solutions through VMR®. Contact us today for more information About VMR®.</p>
</div>
<div class="abs btn welcome-btn">READ MORE</div>
<div class="abs video-frame">
  <div class="video-fill" role="img" aria-label="Therapist applying kinesiology tape to a patient's ankle">
    <svg class="play" width="46" height="46" viewBox="0 0 46 46"><circle cx="23" cy="23" r="22" fill="rgba(255,255,255,.55)"/><path d="M18 14l14 9-14 9z" fill="#fff"/></svg>
  </div>
</div>

<section class="abs services">
  <h2>OUR SERVICES</h2>
  <div class="cards">
    <div class="card"><div class="card-img c1" role="img" aria-label="Therapist stretching an athlete's leg"></div><h3>SPORTS THERAPY</h3></div>
    <div class="card"><div class="card-img c2" role="img" aria-label="Woman exercising with a resistance band"></div><h3>PHYSICAL THERAPY</h3></div>
    <div class="card"><div class="card-img c3" role="img" aria-label="Therapist treating a patient's back"></div><h3>MUSCULAR REHAB</h3></div>
    <div class="card"><div class="card-img c4" role="img" aria-label="Nutritionist with fresh fruit"></div><h3>NUTRITION PLANS</h3></div>
  </div>
</section>

<div class="abs tissue-frame"><div class="tissue-fill" role="img" aria-label="Runner holding an injured knee on a grass field"></div></div>
<h2 class="abs tissue-title">SOFT TISSUE INJURIES</h2>
<div class="abs tissue-copy">
  <p>Third page- Training and Nutrition- At Kestrel Motion we focus on our ability to train individuals from beginners to elite athletes. We have everything you here to attain your fitness goals! False advertisements, 3 month workout fads, insane diets pills, and Elective Surgery are not the way to a healthy sustainable lifestyle. Affordable training is on a person by person basis and comes with nutrition plans custom made for you. Come train with us!</p>
  <p>We build relationships with companies committed to the sustainable health of their employees and patrons. We offer Corporate Health Solutions through VMR®. Contact us today for more information About VMR®.</p>
</div>
<div class="abs btn tissue-btn">READ MORE</div>

<section class="abs partners" aria-label="Partners">
  <div class="badge b1"><div class="shape" style="width:120px;background:#8a8a8a"></div></div>
  <div class="badge b2"><div class="shape" style="width:90px;background:#c9302c"></div><div class="shape" style="width:96px;background:#e6e6e6"></div></div>
</section>

<footer class="abs footer">
  <h4 style="left:133px">CONTACT US</h4>
  <ul class="fcol contact-list">
    <li><svg width="12" height="12" viewBox="0 0 24 24"><path fill="#444" d="M6.6 10.8a15 15 0 0 0 6.6 6.6l2.2-2.2a1 1 0 0 1 1-.25 11.4 11.4 0 0 0 3.6.6 1 1 0 0 1 1 1V20a1 1 0 0 1-1 1A17 17 0 0 1 3 4a1 1 0 0 1 1-1h3.5a1 1 0 0 1 1 1c0 1.25.2 2.45.6 3.6a1 1 0 0 1-.25 1z"/></svg>(555)214-0387</li>
    <li><svg width="12" height="12" viewBox="0 0 24 24"><path fill="#444" d="M6 3h12v5H6zM3 9h18v8h-3v4H6v-4H3zm5 6v4h8v-4z"/></svg>(555)214-0387</li>
    <li><svg width="12" height="12" viewBox="0 0 24 24"><path fill="#444" d="M2 5h20v14H2zm2 2v1l8 5 8-5V7l-8 5z"/></svg><a>info@kestrelmotion.example</a></li>
    <li><svg width="12" height="12" viewBox="0 0 24 24"><path fill="#444" d="M12 2a7 7 0 0 1 7 7c0 5-7 13-7 13S5 14 5 9a7 7 0 0 1 7-7zm0 4a3 3 0 1 0 0 6 3 3 0 0 0 0-6z"/></svg><span>402 W. Alder Ave Suite<br>California, 90000</span></li>
  </ul>
  <h4 style="left:386px">QUICK LINKS</h4>
  <ul class="fcol links">
    <li>Home</li><li>Services</li><li>Physical Therapy</li><li>Personal Training</li><li>Nutrition</li><li>Contact us</li>
  </ul>
  <h4 style="left:565px">NEWSLETTER</h4>
  <p class="fcol news">Enter your email address to receive the latest news and notes from our blog.</p>
  <div class="mail-input">Enter Your Mail Id</div>
  <div class="abs btn subscribe">SUBSCRIBE</div>
  <div class="abs socials" aria-label="Social media links"><span></span><span></span><span></span><span></span><span></span></div>
  <div class="abs rule"></div>
  <p class="abs copy">©2017 Kestrel Motion.All Rights Reserved.</p>
</footer>

</body>
</html>
```